Corporate Business Card

Very professional, Modern, Not to busy, include phone address email, website
(253) 617-4930, 18761 52nd Avenue S, Kent, WA 98047, martin@plumlinegroup.com, varkoworks.com

Target Market(s)

Manufacturing

Industry/Entity Type

Aero, machining, manufacturing, Off road racing

Contact Information for Business Card

Phone, address email, website

```html
<!DOCTYPE html>
<html lang="en">
<head>
<meta charset="utf-8">
<title>Varko Works — Business Card</title>
<link href="https://fonts.googleapis.com/css2?family=Orbitron:wght@700&family=Roboto:wght@400&display=swap" rel="stylesheet">
<style>
  :root {
    --backdrop: #2b2b2c;
    --navy: #2c3a6a;
    --navy-deep: #233160;
    --navy-light: #33427a;
    --white: #f2f3f6;
    --text-soft: #dde1ea;
    --red: #d5272d;
  }
  html, body {
    margin: 0;
    padding: 0;
    width: 1200px;
    height: 1138px;
    overflow: hidden;
    background: var(--backdrop);
  }
  .canvas {
    position: relative;
    width: 1200px;
    height: 1138px;
  }
  .card {
    position: absolute;
    border-radius: 16px;
    overflow: hidden;
  }
  .card--front {
    left: 274px;
    top: 186px;
    width: 623px;
    height: 376px;
  }
  .card--back {
    left: 276px;
    top: 608px;
    width: 618px;
    height: 374px;
    background: linear-gradient(180deg, var(--navy) 0%, var(--navy-deep) 100%);
  }
  .front-field {
    position: absolute;
    inset: 0;
    background: linear-gradient(135deg, var(--navy-deep) 0%, var(--navy-light) 55%, var(--navy) 100%);
  }
  .wordmark {
    position: absolute;
    font-family: "Orbitron", sans-serif;
    font-weight: 700;
    color: var(--white);
    letter-spacing: 1px;
    white-space: nowrap;
    margin: 0;
  }
  .card--front .wordmark {
    left: 52px;
    top: 282px;
    font-size: 34px;
  }
  .card--back .wordmark {
    left: 40px;
    top: 82px;
    font-size: 32px;
  }
  .holder-name {
    position: absolute;
    right: 47px;
    top: 80px;
    margin: 0;
    font-family: "Orbitron", sans-serif;
    font-weight: 700;
    font-size: 22px;
    letter-spacing: 0.5px;
    color: var(--white);
  }
  .holder-name .surname { color: var(--red); }
  .contact-list {
    position: absolute;
    right: 46px;
    top: 230px;
    margin: 0;
    padding: 0;
    list-style: none;
    font-family: "Roboto", sans-serif;
    font-size: 16.5px;
    color: var(--text-soft);
  }
  .contact-list li {
    display: flex;
    justify-content: flex-end;
    align-items: center;
    height: 24.5px;
  }
  .contact-list svg {
    width: 14px;
    height: 14px;
    margin-left: 16px;
    fill: var(--red);
    flex: none;
  }
</style>
</head>
<body>
<div class="canvas">

  <section class="card card--front">
    <div class="front-field" role="img" aria-label="Embossed repeating brand name pattern in tonal navy"></div>
    <p class="wordmark">VARKO WORKS</p>
  </section>

  <section class="card card--back">
    <p class="wordmark">VARKO WORKS</p>
    <h1 class="holder-name">MARTIN <span class="surname">HALE</span></h1>
    <ul class="contact-list">
      <li>(253) 617-4930
        <svg viewBox="0 0 16 16" aria-hidden="true"><path d="M2 6c0-2 2-3 6-3s6 1 6 3v1h-3V5.5H5V7H2zM4 8h8l2 6H2z"/></svg>
      </li>
      <li>martin@plumlinegroup.com
        <svg viewBox="0 0 16 16" aria-hidden="true"><path d="M1 3h14v10H1zM2.5 4.5 8 9l5.5-4.5v1L8 10 2.5 5.5z" fill-rule="evenodd"/></svg>
      </li>
      <li>www.varkoworks.com
        <svg viewBox="0 0 16 16" aria-hidden="true"><path d="M8 1a7 7 0 1 0 0 14A7 7 0 0 0 8 1zm0 1.5c.9 1 1.5 2.6 1.7 4.5H6.3C6.5 5.1 7.1 3.5 8 2.5zM2.6 7a5.5 5.5 0 0 1 2.7-4c-.6 1.1-1 2.5-1 4zm0 2h1.7c0 1.5.4 2.9 1 4a5.5 5.5 0 0 1-2.7-4zM8 13.5c-.9-1-1.5-2.6-1.7-4.5h3.4c-.2 1.9-.8 3.5-1.7 4.5zM10.7 13c.6-1.1 1-2.5 1-4h1.7a5.5 5.5 0 0 1-2.7 4zm1-6c0-1.5-.4-2.9-1-4a5.5 5.5 0 0 1 2.7 4z"/></svg>
      </li>
      <li>18761 52nd Avenue S, Kent, WA 98047
        <svg viewBox="0 0 16 16" aria-hidden="true"><path d="M8 1a5 5 0 0 0-5 5c0 3.5 5 9 5 9s5-5.5 5-9a5 5 0 0 0-5-5zm0 7a2 2 0 1 1 0-4 2 2 0 0 1 0 4z"/></svg>
      </li>
    </ul>
  </section>

</div>
</body>
</html>
```